TK Stationery - Modern Contemporary

Develop modern template for Letterhead and Stationery (business card, letterhead, envelopes) using the TK Logo and Icon

Colors
0054AA
0677BA
7BADD7
CADEEF
E8F1F8
00AB8E
00BBA5
67D7C9
C6EFE9
E9F9F6
EE7325
F08F49
F5BC92
FAE3D3
FDF4ED
6B429C
8869AF
B7A5CE
E3DAEB
F3F0F8

```html
<!DOCTYPE html>
<html lang="en">
<head>
<meta charset="utf-8">
<title>TK Stationery</title>
<link href="https://fonts.googleapis.com/css2?family=Prata&family=Questrial&display=swap" rel="stylesheet">
<style>
  :root {
    --navy: #2a2f4a;
    --green: #21c172;
    --ink: #5a5d6b;
    --paper: #ffffff;
    --paper-shade: #e6e6e6;
    --bg-light: #d4d4d4;
    --bg-dark: #8a8a8a;
  }
  * { margin: 0; padding: 0; box-sizing: border-box; }
  html, body { width: 1200px; height: 806px; overflow: hidden; }
  body {
    position: relative;
    background: linear-gradient(90deg, var(--bg-light) 0%, #a8a8a8 45%, var(--bg-dark) 100%);
    font-family: "Questrial", sans-serif;
    color: var(--ink);
  }
  .sheet {
    position: absolute;
    background: linear-gradient(100deg, var(--paper) 35%, var(--paper-shade) 100%);
    box-shadow: 0 2px 8px rgba(0,0,0,0.18);
    overflow: hidden;
  }
  .brand-name {
    font-family: "Prata", serif;
    color: var(--navy);
    letter-spacing: 0.5px;
    white-space: nowrap;
    line-height: 1;
  }
  .brand-bar {
    position: absolute; left: 0; right: 0; bottom: 0; height: 7px;
    display: flex;
  }
  .brand-bar span:first-child { flex: 1; background: var(--navy); }
  .brand-bar span:last-child { flex: 1; background: var(--green); margin-left: 2px; }

  /* Letterhead */
  .letterhead { left: 77px; top: 108px; width: 450px; height: 630px; }
  .letterhead .brand-name { position: absolute; left: 47px; top: 64px; font-size: 29px; }
  .contact { position: absolute; left: 301px; top: 40px; font-size: 9.2px; line-height: 11.4px; color: #555; }
  .contact .address { margin-bottom: 4px; }
  .contact li { list-style: none; display: flex; align-items: center; gap: 5px; }
  .contact svg { width: 8px; height: 8px; fill: var(--green); flex: none; }
  .letter { position: absolute; left: 41px; top: 202px; width: 371px; }
  .salutation { font-size: 12px; color: #444; margin-bottom: 17px; }
  .letter p.body { font-size: 6.2px; line-height: 9.6px; color: #777; margin-bottom: 9.5px; text-align: justify; }
  .closing { font-size: 6.2px; color: #777; margin-top: 16px; }

  /* Envelope back */
  .envelope-back { left: 609px; top: 115px; width: 516px; height: 235px; background: linear-gradient(100deg, #fafafa, #e9e9e9); }
  .flap { position: absolute; left: 0; top: 0; width: 100%; }
  .flap-label { position: absolute; left: 0; right: 0; text-align: center; font-size: 20px; color: #fff; }
  .envelope-back .flap-label { top: 26px; }

  /* Envelope front (flap open) */
  .envelope-open { left: 568px; top: 236px; width: 517px; height: 236px; }
  .envelope-open .flap-label { top: 22px; }

  /* Envelope face */
  .envelope-face { left: 568px; top: 504px; width: 517px; height: 234px; }
  .envelope-face .brand-name { position: absolute; left: 38px; top: 32px; font-size: 27px; }
  .envelope-face .address { position: absolute; left: 38px; top: 62px; font-size: 9.2px; line-height: 11.4px; color: #555; }
</style>
</head>
<body>

  <section class="sheet letterhead" aria-label="Letterhead">
    <div class="brand-name">tika kora</div>
    <ul class="contact">
      <li class="address">2140 Linden Court<br>Juneau, Alaska 34100</li>
      <li><svg viewBox="0 0 10 10"><path d="M2 0.5l2 2-1 1.3c.7 1.5 1.7 2.5 3.2 3.2L7.5 6l2 2-1.3 1.5C4.5 9.2 0.8 5.5 0.5 1.8z"/></svg>555-214-7730</li>
      <li><svg viewBox="0 0 10 10"><path d="M2.5 0h5v10h-5zM3.5 1v7h3V1z"/></svg>555-310-6642</li>
      <li><svg viewBox="0 0 10 10"><path d="M0 2h10v6H0zM1 3l4 3 4-3v-.2H1z"/></svg>hello@tikakora.com</li>
      <li><svg viewBox="0 0 10 10"><circle cx="5" cy="5" r="4.5" fill="none" stroke="#21c172" stroke-width="1"/><path d="M0.5 5h9M5 .5v9" stroke="#21c172" stroke-width=".8"/></svg>www.tikakora.com</li>
    </ul>
    <div class="letter">
      <p class="salutation">Dear Mr. Hale,</p>
      <p class="body">Thank you for meeting with our team last week. We enjoyed hearing about your plans for the new season and the goals you shared for the coming year. Please find a short summary of our proposal below, along with the next steps we discussed together.</p>
      <p class="body">Our studio will prepare the first drafts within two weeks. Each draft includes notes on layout, colour and type, so your staff can review the options with ease and share any changes they would like us to make before the final round.</p>
      <p class="body">Once the drafts are approved, we will move to print and delivery. We will send samples of paper stock and finish to your office so the whole team can see and feel the results before we place the full order with our printer.</p>
      <p class="body">If you have any questions, please call or write to us at any time. We look forward to working with you.</p>
      <p class="closing">Sincerely,</p>
    </div>
    <div class="brand-bar"><span></span><span></span></div>
  </section>

  <section class="sheet envelope-back" aria-label="Envelope back">
    <svg class="flap" viewBox="0 0 516 74" height="74" aria-hidden="true">
      <path d="M0 0H516L500 50Q492 74 466 74H50Q24 74 16 50Z" fill="var(--green)"/>
    </svg>
    <div class="flap-label brand-name" style="color:#fff">tika kora</div>
  </section>

  <section class="sheet envelope-open" aria-label="Envelope with flap">
    <svg class="flap" viewBox="0 0 517 73" height="73" aria-hidden="true">
      <path d="M0 0H517L502 48Q494 73 468 73H48Q22 73 14 48Z" fill="var(--navy)"/>
    </svg>
    <div class="flap-label brand-name" style="color:#fff">tika kora</div>
  </section>

  <section class="sheet envelope-face" aria-label="Envelope front">
    <div class="brand-name">tika kora</div>
    <div class="address">2140 Linden Court<br>Juneau, Alaska 34100</div>
    <div class="brand-bar"><span></span><span></span></div>
  </section>

</body>
</html>
```